UK landscaping company needs website

We, Brackwell Landscapes need a website design for a company based in Surrey, UK. The design should be bold and playful. We have three main areas of work driveways, paving and fencing. It shouldn't be too heavy in text and concentrate on the pictures from previous jobs we've completed. You may use stock images for the design, these can be changed if you are successful. Please don’t just copy the flyer it is just there to provide content.
We have a logo design which we would also like editing slightly.
Here are some of my local competitors
https://www.pelmarlandscapes.example.co.uk/

https://www.twinfirgardendesign.example.com/

https://kestbyrnlandscapes.example.co.uk/

Industry/Entity Type

Landscaping

Coding

Coded - Design and coding required

Number of Pages Required

3 page

Font styles to use
Sans Serif

Requirements
Must have
• Pictures of my previous jobs.
Must be mobile friendly
Easy to navigate
Nice to have
• Try to use different colours. It would be good to have some designs that aren’t just black and green.
I’d like some curves in the design.
Should not have
• We install hard landscaping. Think more building/construction and less plants and cutting grass.

```html
<!DOCTYPE html>
<html lang="en">
<head>
<meta charset="utf-8">
<title>Brackwell Landscapes – Our Services</title>
<link rel="stylesheet" href="https://fonts.googleapis.com/css2?family=Rubik:wght@400;500;700&display=swap">
<style>
:root{
  --green:#5cb82c;
  --green-soft:#7cc655;
  --dark:#2a2a2a;
  --ink:#222222;
  --text:#3a3a3a;
  --grey-band:#ececec;
  --white:#ffffff;
}
*{box-sizing:border-box;margin:0;padding:0}
html,body{width:1200px;height:3041px;overflow:hidden}
body{position:relative;font-family:"Rubik",Arial,sans-serif;color:var(--text);background:var(--white)}
.abs{position:absolute}

/* header */
.site-header{position:absolute;top:0;left:0;width:1200px;height:71px;background:var(--dark);z-index:5}
.brand{position:absolute;left:130px;top:14px;color:var(--white);font-weight:700;font-size:24px;line-height:1;letter-spacing:.5px}
.brand small{display:block;font-size:10px;letter-spacing:2px;margin-top:6px;font-weight:700}
.main-nav{position:absolute;top:27px;left:475px;display:flex;gap:0}
.main-nav a{color:var(--white);text-decoration:none;font-weight:500;font-size:16px;letter-spacing:-.3px;margin-right:43px}
.main-nav a.active{color:var(--green);text-decoration:underline}
.estimate-box{position:absolute;right:0;top:0;width:201px;height:71px;background:var(--green);color:var(--white);padding:14px 0 0 28px}
.estimate-box span{display:block;font-size:15px;font-weight:500;letter-spacing:-.3px}
.estimate-box strong{display:block;font-size:22px;font-weight:500;margin-top:2px}

/* hero */
.hero-photo{position:absolute;top:71px;left:0;width:1200px;height:640px;
  background:linear-gradient(100deg,#5a3c22 0%,#7a5634 35%,#8f6a43 55%,#6f8f3a 75%,#5aa23a 100%)}
.hero-curve{position:absolute;top:0;left:0;z-index:2}

.intro{position:absolute;top:605px;left:0;width:1200px;text-align:center;z-index:3}
.intro h1{font-size:46px;font-weight:500;color:var(--ink);letter-spacing:-.5px}
.intro h1 em{font-style:normal;color:var(--green)}
.intro p{width:680px;margin:22px auto 0;font-size:14.5px;line-height:24px;color:var(--text)}

/* service rows */
.band{position:absolute;left:0;width:1200px}
.band.grey{background:var(--grey-band)}
.photo-frame{position:absolute;width:356px;height:356px;border-radius:50%;background:var(--green)}
.photo-frame .ring{position:absolute;inset:20px;border-radius:50%;background:var(--white)}
.photo-frame .photo{position:absolute;inset:26px;border-radius:50%}
.service-title{position:absolute;font-size:38px;font-weight:500;color:var(--ink);letter-spacing:-.5px}
.ticks{position:absolute;list-style:none;width:380px}
.ticks li{position:relative;padding-left:27px;font-size:15.5px;line-height:24px;color:var(--text);margin-bottom:23px}
.ticks li svg{position:absolute;left:0;top:6px}

/* cta */
.cta{position:absolute;top:2250px;left:0;width:1200px;height:438px;
  background:linear-gradient(135deg,#7dc559 0%,#6cb845 45%,#5aa735 100%)}
.cta-curve{position:absolute;top:0;left:0}
.cta-copy{position:absolute;top:2460px;left:0;width:1200px;text-align:center;color:var(--white);font-weight:700;font-size:30px;line-height:43px;letter-spacing:-1.2px}
.cta-button{position:absolute;top:2560px;left:479px;width:242px;height:46px;background:var(--dark);border-radius:3px;color:var(--white);font-size:17px;font-weight:500;display:flex;align-items:center;justify-content:center;gap:12px;text-decoration:none}

/* footer */
.site-footer{position:absolute;top:2688px;left:0;width:1200px;height:353px;background:var(--dark);color:var(--white)}
.footer-brand{position:absolute;left:132px;top:82px;font-size:36px;font-weight:700;line-height:1}
.footer-brand small{display:block;font-size:13px;letter-spacing:2px;margin-top:8px}
.footer-col{position:absolute;top:72px}
.footer-col h4{font-size:15px;font-weight:500;margin-bottom:12px;letter-spacing:-.3px}
.footer-col a{display:block;color:var(--white);font-size:13px;text-decoration:underline;margin-bottom:9px}
.footer-col.main a{font-size:15px;font-weight:500;text-decoration:none;margin-bottom:18px;letter-spacing:-.3px}
.footer-map{position:absolute;left:787px;top:73px;width:281px;height:109px;background:linear-gradient(135deg,#dfe7ee,#c9d9e6 60%,#e8e3d3);border-bottom:3px solid #f0c040}
.socials{position:absolute;top:235px;left:525px;display:flex;gap:7px}
.socials span{width:32px;height:32px;border:1.5px solid #bbbbbb;border-radius:50%}
.footer-rule{position:absolute;left:28px;right:28px;top:296px;height:1px;background:#555}
.copyright{position:absolute;top:315px;width:1200px;text-align:center;font-size:14px;color:#cfcfcf}
</style>
</head>
<body>

<header class="site-header">
  <div class="brand">BRACKWELL<small>LANDSCAPES</small></div>
  <nav class="main-nav">
    <a href="#">HOME</a><a href="#">SERVICES</a><a href="#" class="active">ABOUT</a><a href="#">OUR WORK</a><a href="#">CONTACT</a>
  </nav>
  <div class="estimate-box"><span>FREE ESTIMATES</span><strong>07700 900418</strong></div>
</header>

<div class="hero-photo" role="img" aria-label="Photo of a new timber feature fence with a gravel border and lawn"></div>
<svg class="hero-curve" width="1200" height="880" viewBox="0 0 1200 880">
  <defs>
    <radialGradient id="heroShade" cx="0.5" cy="0.62" r="0.5">
      <stop offset="0" stop-color="#dcdcdc"/><stop offset="1" stop-color="#ffffff"/>
    </radialGradient>
  </defs>
  <path d="M0,650 C300,480 680,380 1200,480 L1200,880 L0,880 Z" fill="var(--green)"/>
  <path d="M0,668 C330,520 680,438 1200,492 L1200,880 L0,880 Z" fill="#ffffff"/>
  <path d="M250,560 C450,470 700,440 1000,470 C800,520 500,540 250,560 Z" fill="url(#heroShade)" opacity=".6"/>
</svg>

<section class="intro">
  <h1>OUR <em>SERVICES</em></h1>
  <p>Brackwell Landscapes offer a comprehensive range of landscaping services. They include paving and brickwork, fencing, decking, pergolas, artificial grass, driveways, and turfing and planting. We work with garden designers but working closely with our customers we feel they aren't always necessary to achieve an outstanding finished project.</p>
</section>

<!-- Driveways -->
<section class="band grey" style="top:860px;height:470px"></section>
<div class="photo-frame" style="left:212px;top:915px">
  <div class="ring"></div>
  <div class="photo" role="img" aria-label="Photo of a grey block-paved driveway with curved edging" style="background:linear-gradient(160deg,#7e8a6f 0%,#6d6f73 30%,#5c5f66 70%,#8a8a86 100%)"></div>
</div>
<h2 class="service-title" style="left:645px;top:987px">DRIVEWAYS</h2>
<ul class="ticks" style="left:650px;top:1062px">
  <li><svg width="16" height="12" viewBox="0 0 16 12"><path d="M1.5,6 L6,10.5 L14.5,1.5" fill="none" stroke="var(--green)" stroke-width="2.6"/></svg>We cater for every budget. You can increase the value of your home with a relatively small investment.</li>
  <li><svg width="16" height="12" viewBox="0 0 16 12"><path d="M1.5,6 L6,10.5 L14.5,1.5" fill="none" stroke="var(--green)" stroke-width="2.6"/></svg>All our driveways are built to last!</li>
</ul>

<!-- Paving -->
<div class="photo-frame" style="left:632px;top:1392px">
  <div class="ring"></div>
  <div class="photo" role="img" aria-label="Photo of a sandstone patio with a circular paving feature" style="background:linear-gradient(170deg,#8a8f86 0%,#a99488 35%,#b59a8c 65%,#7a9a4a 100%)"></div>
</div>
<h2 class="service-title" style="left:185px;top:1464px">PAVING</h2>
<ul class="ticks" style="left:183px;top:1540px">
  <li><svg width="16" height="12" viewBox="0 0 16 12"><path d="M1.5,6 L6,10.5 L14.5,1.5" fill="none" stroke="var(--green)" stroke-width="2.6"/></svg>We have a vast knowledge of paving materials, helping you make the right choices.</li>
  <li><svg width="16" height="12" viewBox="0 0 16 12"><path d="M1.5,6 L6,10.5 L14.5,1.5" fill="none" stroke="var(--green)" stroke-width="2.6"/></svg>We can help you transform your garden giving you a functional and attractive space.</li>
</ul>

<!-- Fencing -->
<section class="band grey" style="top:1820px;height:480px"></section>
<div class="photo-frame" style="left:212px;top:1877px">
  <div class="ring"></div>
  <div class="photo" role="img" aria-label="Photo of a new timber fence beside a gravel path and lawn" style="background:linear-gradient(150deg,#6b7a5a 0%,#8a6a45 35%,#9a7650 60%,#6aa83e 100%)"></div>
</div>
<h2 class="service-title" style="left:645px;top:1941px">FENCING</h2>
<ul class="ticks" style="left:650px;top:2013px">
  <li><svg width="16" height="12" viewBox="0 0 16 12"><path d="M1.5,6 L6,10.5 L14.5,1.5" fill="none" stroke="var(--green)" stroke-width="2.6"/></svg>We offer all aspects of fencing, installed to an extremely high standard.</li>
  <li><svg width="16" height="12" viewBox="0 0 16 12"><path d="M1.5,6 L6,10.5 L14.5,1.5" fill="none" stroke="var(--green)" stroke-width="2.6"/></svg>From the smallest post to the largest fence, we provide a prompt and friendly fencing service you can depend on.</li>
</ul>

<!-- Call to action -->
<section class="cta" role="img" aria-label="Photo of a finished garden with paving, pergola posts and artificial grass, tinted green">
  <svg class="cta-curve" width="1200" height="438" viewBox="0 0 1200 438">
    <path d="M0,0 H1200 V95 C900,20 500,40 0,280 Z" fill="var(--grey-band)"/>
    <path d="M0,280 C500,40 900,20 1200,95 L1200,110 C900,45 500,70 0,300 Z" fill="var(--green)"/>
  </svg>
</section>
<div class="cta-copy">YOUR GARDEN AND DRIVEWAY CARED FOR<br>THE WAY THEY SHOULD BE</div>
<a class="cta-button" href="#">START MY ESTIMATE
  <svg width="17" height="17" viewBox="0 0 17 17"><circle cx="8.5" cy="8.5" r="8" fill="#fff"/><path d="M7,5 L10.5,8.5 L7,12" fill="none" stroke="var(--dark)" stroke-width="2"/></svg>
</a>

<footer class="site-footer">
  <div class="footer-brand">BRACKWELL<small>LANDSCAPES</small></div>
  <div class="footer-col main" style="left:385px;top:73px">
    <a href="#">HOME</a><a href="#">ABOUT US</a><a href="#">OUR WORK</a><a href="#">CONTACT</a>
  </div>
  <div class="footer-col" style="left:505px">
    <h4>SERVICES</h4><a href="#">Driveways</a><a href="#">Paving</a><a href="#">Fencing</a>
  </div>
  <div class="footer-col" style="left:633px">
    <h4>QUICK LINKS</h4><a href="#">FAQ</a><a href="#">Testimonials</a><a href="#">Sitemap</a>
  </div>
  <div class="footer-map" role="img" aria-label="Map showing the business location"></div>
  <div class="socials"><span></span><span></span><span></span><span></span></div>
  <div class="footer-rule"></div>
  <p class="copyright">© 2020 Brackwell Landscapes. All Rights are Reserved.</p>
</footer>

</body>
</html>
```